New profile page for existing party website

For the party website 'Partyvenz' we need a new design for the user profile page.

The page should show
* a profile picture
* basic information like name, age and city
* music styles he/she likes
* links to their Chatterbook profile and website
* a bio (HTML content)
* events they plan to go to
* past events
* pictures

Challenge is that some users may have little information (just their name) while others have a huge description, lots of foto's, events, etc.

Please visit http://www.partyvenz.example and http://www.partyvenz.example/users/bertil

Target Market(s)

Men and women between 18 and 35

Industry/Entity Type

Night Club

Number of Pages Required

2 page

Font styles to use
Other font styles liked:
• Roboto

Requirements
Must have
• Please design how the page looks with a fully filled out profile and with an empty profile.
• It should fit well with the existing website.
• Include designs for both for small screens (mobile) and large screens (tablet, desktop).
Nice to have
• UX design on how to collapse or paginate sections.
• Interactive effects would be a bonus.
Should not have
• The page should not have subnavigation like menus or tabs.

```html
<!DOCTYPE html>
<html lang="nl">
<head>
<meta charset="utf-8">
<title>MarcoV Photography – Partyvenz profiel</title>
<link rel="stylesheet" href="https://fonts.googleapis.com/css2?family=Roboto:wght@400;500;700&family=Roboto+Condensed:wght@400;700&family=Open+Sans:ital,wght@0,400;0,600;1,400&family=Raleway:wght@500;700&display=swap">
<style>
:root{
  --black:#0d0d0d;
  --white:#ffffff;
  --ink:#333333;
  --muted:#666666;
  --soft:#8a8a8a;
  --band:#eeeeee;
  --orange:#ee8625;
  --footer:#2b2b2b;
  --dark-btn:#222222;
}
*{margin:0;padding:0;box-sizing:border-box}
html,body{width:1200px;height:2699px;overflow:hidden;background:var(--white);font-family:'Open Sans',sans-serif;color:var(--ink)}
.page{position:relative;width:1200px;height:2699px}
header,section,footer{position:relative}
.wrap{position:relative;width:1002px;margin:0 auto;height:100%}

/* top bar */
.topbar{height:81px;background:var(--black);color:var(--white);z-index:3}
.brand{position:absolute;left:0;top:22px;font-family:'Roboto',sans-serif;font-weight:700;font-size:34px;color:var(--white);letter-spacing:-.5px}
.mainnav{position:absolute;left:190px;top:30px;display:flex;gap:32px;font-family:'Roboto',sans-serif;font-weight:500;font-size:13px;letter-spacing:.3px}
.usernav{position:absolute;right:0;top:20px;display:flex;align-items:center;gap:22px;font-family:'Roboto',sans-serif;font-weight:500;font-size:12px}
.usernav span{display:flex;align-items:center;gap:6px}
.nav-avatar{width:32px;height:32px;border-radius:50%;border:2px solid var(--white);background:linear-gradient(135deg,#a66a4f,#5d3428)}
.search-btn{width:36px;height:36px;border-radius:50%;border:2px solid var(--white);display:flex;align-items:center;justify-content:center}

/* hero */
.hero{height:274px;background:radial-gradient(ellipse at 70% 20%,#7a6a8c 0%,#3a2e4a 35%,#1a1420 70%),#15101c;color:var(--white);z-index:2}
.hero-title{position:absolute;left:213px;top:136px;font-family:'Roboto',sans-serif;font-weight:500;font-size:42px;line-height:48px;letter-spacing:1.5px}
.hero-meta{position:absolute;left:214px;top:191px;font-family:'Roboto',sans-serif;font-size:14px}
.hero-meta b{font-weight:400;margin:0 8px}
.hero-links{position:absolute;left:214px;top:225px;display:flex;gap:28px;font-family:'Roboto',sans-serif;font-size:17px}
.hero-links span{display:flex;align-items:center;gap:9px}
.avatar{position:absolute;left:0;top:142px;width:190px;height:190px;border-radius:50%;border:6px solid var(--white);background:linear-gradient(160deg,#4d5a6a 0%,#b8a89a 50%,#3c3c3c 100%);z-index:2}

.profile-bar{height:95px;background:var(--band);border-bottom:1px solid #ddd;z-index:1}
.profile-bio{position:absolute;left:214px;top:18px;width:360px;font-size:12.5px;line-height:20px;color:var(--muted)}
.profile-stats{position:absolute;right:0;top:25px;display:flex;gap:30px;font-style:italic;font-size:15px;color:var(--soft)}
.profile-stats span{display:flex;align-items:center;gap:7px}

/* intro */
.intro{height:549px}
.section-title{font-family:'Roboto Condensed',sans-serif;font-weight:400;font-size:32px;text-align:center;color:#222;letter-spacing:.5px}
.intro .section-title{position:absolute;top:40px;width:100%}
.intro-text{position:absolute;top:88px;left:0;width:100%;text-align:center;font-size:11.5px;line-height:20px;color:var(--muted)}
.video{position:absolute;left:0;top:189px;width:482px;height:294px;border:5px solid #e4e4e4;box-shadow:0 0 0 1px #ccc}
.video-img{position:absolute;inset:0;background:linear-gradient(135deg,#c21f9a 0%,#3a1a6e 40%,#151530 70%,#2a3c7a 100%)}
.play{position:absolute;left:210px;top:120px;width:54px;height:34px;background:rgba(90,90,90,.85);border-radius:4px;display:flex;align-items:center;justify-content:center}
.progress{position:absolute;left:38px;right:120px;bottom:32px;height:6px;background:rgba(255,255,255,.35)}
.progress i{display:block;width:58%;height:100%;background:#5fa8d8}
.info{position:absolute;left:522px;top:208px;width:480px}
.info h3{font-family:'Roboto Condensed',sans-serif;font-weight:400;font-size:26px;letter-spacing:.5px;color:#222;margin-bottom:20px}
.info p{font-size:11.5px;line-height:20px;color:var(--muted);margin-bottom:10px}

/* conditions */
.conditions{height:390px;background:radial-gradient(ellipse at 50% 40%,#4e2f63 0%,#2f1d3c 50%,#1a121e 100%);color:var(--white);text-align:center}
.conditions h2{position:absolute;top:78px;left:0;width:100%;font-family:'Roboto Condensed',sans-serif;font-weight:400;font-size:40px;line-height:48px;letter-spacing:1px}
.conditions ul{position:absolute;top:136px;left:0;width:100%;list-style:none;font-family:'Roboto',sans-serif;font-weight:500;font-size:16px;line-height:29px}

/* signup */
.signup{height:146px;background:#f1f1f1}
.signup h2{position:absolute;left:0;top:48px;font-family:'Roboto Condensed',sans-serif;font-weight:400;font-size:35px;color:#333;letter-spacing:.5px}
.signup p{position:absolute;left:207px;top:44px;width:795px;font-size:11.5px;line-height:20px;color:var(--muted)}

/* events */
.events{height:473px}
.events .section-title{position:absolute;top:56px;width:100%;font-size:26px}
.cards{position:absolute;top:118px;left:0;width:100%;display:flex;justify-content:space-between}
.card{width:310px}
.card-img{position:relative;height:190px}
.date{position:absolute;left:12px;bottom:12px;width:58px;height:66px;background:rgba(150,30,30,.8);color:var(--white);text-align:center;font-family:'Roboto',sans-serif;line-height:1}
.date em{display:block;font-style:normal;font-size:10px;padding-top:7px}
.date strong{display:block;font-size:27px;font-weight:500;margin:3px 0}
.date small{display:block;font-size:11px}
.card h4{margin-top:26px;font-family:'Roboto',sans-serif;font-weight:400;font-size:19px;letter-spacing:.3px;color:#222}
.card-meta{margin-top:12px;display:flex;gap:24px;font-style:italic;font-size:12px;color:var(--muted)}
.card-meta span{display:flex;align-items:center;gap:6px}
.card p{margin-top:12px;font-size:11.5px;line-height:19px;color:var(--muted)}

/* gallery */
.gallery-title{height:84px}
.gallery-title h2{position:absolute;top:26px;width:100%;font-family:'Roboto',sans-serif;font-weight:400;font-size:31px;text-align:center;color:#333}
.gallery{display:flex;height:312px}
.gallery div{flex:1}

/* newsletter */
.newsletter{height:146px;background:var(--orange);color:var(--white)}
.nl-icon{position:absolute;left:0;top:48px}
.nl-label{position:absolute;left:75px;top:50px;font-family:'Raleway',sans-serif;line-height:1}
.nl-label span{display:block;font-weight:500;font-size:17px;letter-spacing:.5px}
.nl-label strong{display:block;font-weight:700;font-size:23px;margin-top:6px;letter-spacing:.5px}
.nl-field{position:absolute;top:55px;height:40px;background:var(--white);color:#999;font-size:10px;letter-spacing:.5px;padding:13px 26px;font-family:'Raleway',sans-serif}
.nl-name{left:273px;width:296px}
.nl-mail{left:575px;width:297px}
.nl-btn{position:absolute;left:878px;top:55px;width:124px;height:40px;background:var(--dark-btn);font-family:'Raleway',sans-serif;font-weight:700;font-size:13px;text-align:center;line-height:40px;letter-spacing:.5px}

/* footer */
.footer{height:149px;background:var(--footer);color:var(--white);text-align:center}
.socials{position:absolute;top:25px;width:100%;display:flex;justify-content:center;gap:9px}
.socials i{width:28px;height:28px;border-radius:50%;background:var(--white);display:block}
.footnav{position:absolute;top:72px;width:100%;font-family:'Roboto',sans-serif;font-weight:500;font-size:11px;letter-spacing:.3px}
.footnav b{font-weight:400;margin:0 12px}
.copyright{position:absolute;top:99px;width:100%;font-size:11px}
.footer-tag{position:absolute;right:-80px;top:75px;font-size:11px}
</style>
</head>
<body>
<div class="page">

  <header class="topbar">
    <div class="wrap">
      <div class="brand">Partyvenz</div>
      <nav class="mainnav"><span>HOME</span><span>AGENDA</span><span>FREE TICKETS</span><span>PHOTOS</span><span>NEWS</span></nav>
      <div class="usernav">
        <span>LOGIN <svg width="10" height="11" viewBox="0 0 10 11"><rect x="1" y="5" width="8" height="6" fill="#fff"/><path d="M3 5V3a2 2 0 0 1 4 0v2" stroke="#fff" stroke-width="1.5" fill="none"/></svg></span>
        <span>MY ACCOUNT <svg width="10" height="11" viewBox="0 0 10 11"><circle cx="5" cy="3" r="2.6" fill="#fff"/><path d="M0 11a5 4.5 0 0 1 10 0z" fill="#fff"/></svg></span>
        <div class="nav-avatar" role="img" aria-label="Kleine profielfoto van de gebruiker"></div>
        <div class="search-btn"><svg width="14" height="14" viewBox="0 0 14 14"><circle cx="6" cy="6" r="4.2" stroke="#fff" stroke-width="2" fill="none"/><path d="M9 9l4 4" stroke="#fff" stroke-width="2"/></svg></div>
      </div>
    </div>
  </header>

  <section class="hero" role="img" aria-label="Sfeerfoto van een feest met lichtshow op de achtergrond">
    <div class="wrap">
      <div class="avatar" role="img" aria-label="Profielfoto van de fotograaf"></div>
      <h1 class="hero-title">MARCOV PHOTOGRAPHY</h1>
      <div class="hero-meta">Member since : May 24, 2006<b>/</b>Age : 34<b>/</b>City : Amsterdam<b>/</b>Music : Latin / Salsa</div>
      <div class="hero-links">
        <span><svg width="18" height="18" viewBox="0 0 18 18"><circle cx="9" cy="9" r="8" fill="#fff"/><path d="M3 7c3 0 4 2 3 4s1 3 2 5M12 2c-1 2 0 4 3 5" stroke="#1a1420" stroke-width="1.6" fill="none"/></svg>Circle</span>
        <span><svg width="16" height="16" viewBox="0 0 16 16"><rect x="1" y="1" width="14" height="14" rx="2" fill="none" stroke="#fff" stroke-width="2"/></svg>Chatterbook</span>
      </div>
    </div>
  </section>

  <section class="profile-bar">
    <div class="wrap">
      <p class="profile-bio">Nemo enim ipsam voluptatem quia voluptas sit aspernatur aut odit aut fugit, sed quia consequuntur</p>
      <div class="profile-stats">
        <span><svg width="15" height="13" viewBox="0 0 15 13"><path d="M7.5 12L1.8 6.5A3.2 3.2 0 0 1 7.5 2.3a3.2 3.2 0 0 1 5.7 4.2z" fill="none" stroke="#8a8a8a" stroke-width="1.3"/></svg>120 Likes</span>
        <span><svg width="15" height="13" viewBox="0 0 15 13"><path d="M2 1h11a1 1 0 0 1 1 1v6a1 1 0 0 1-1 1H6l-3 3V9H2a1 1 0 0 1-1-1V2a1 1 0 0 1 1-1z" fill="none" stroke="#8a8a8a" stroke-width="1.3"/></svg>300 Comments</span>
        <span><svg width="12" height="14" viewBox="0 0 12 14"><rect x="1" y="1" width="10" height="12" fill="none" stroke="#8a8a8a" stroke-width="1.3"/><path d="M3.5 5h5M3.5 8h5" stroke="#8a8a8a" stroke-width="1.2"/></svg>Collecation</span>
      </div>
    </div>
  </section>

  <section class="intro">
    <div class="wrap">
      <h2 class="section-title">WIL JIJ FOTOGRAFEREN VOOR PARTYVENZ?</h2>
      <p class="intro-text">Als je uitgaan leuk vindt, makkelijk bent in de omgang en uiteraard houdt van fotograferen, biedt Partyvenz je de kans een kijkje te nemen in de wereld van de partyfotografie.<br>Door de inzet van de fotografen is Partyvenz uitgegroeid tot een van de meest toonaangevende partysites van Nederland. De betrouwbaarheid, de hoge kwaliteit van de foto's<br>en het coveren van de belangrijkste evenementen maakt van Partyvenz een van de best bezochte websites in ons vakgebied.</p>
      <div class="video">
        <div class="video-img" role="img" aria-label="Videostill van een dj en dansend publiek"></div>
        <div class="play"><svg width="16" height="18" viewBox="0 0 16 18"><path d="M2 1l13 8-13 8z" fill="#fff"/></svg></div>
        <div class="progress"><i></i></div>
      </div>
      <div class="info">
        <h3>BELANGRIJK INFORMATIE</h3>
        <p>Fotograferen voor Partyvenz is op vrijwillige basis. Je kan kiezen waar en wanneer je uitgaat en foto's maakt, maar een vaste inbreng word wel van je verwacht. Hoe meer je voor Partyvenz doet, hoe meer ervaring je opdoet met de camera en hoe beter je word. Hierdoor kan je weer naar interessantere feesten en festivals. Wat je wel krijgt is gratis entree voor een evenement en soms ook andere voordelen zoals gratis drankjes... Je gaat meestal met ze tweetjes op pad en ontmoet veel nieuwe mensen zoals DJ's en organisatoren.</p>
        <p>Hoe meer je voor Partyvenz.nl werkt hoe meer ervaring je er ook uit zal halen. De beste fotografen doen de leukste en de meest uitdagende evenementen bijvoorbeeld: Nachtpaleis, Bassveld Outdoor, Zonnedagen weekend, Meerdans etc.</p>
      </div>
    </div>
  </section>

  <section class="conditions" role="img" aria-label="Sfeerfoto van lachend feestpubliek als achtergrond">
    <h2>VOORWAARDEN</h2>
    <ul>
      <li>Je moet 18 jaar of ouder zijn.</li>
      <li>Je moet het aankunnen om hoge kwaliteit foto's te maken en professioneel gedrag vertonen.</li>
      <li>Je moet sociaal zijn; een open persoon zijn die ervan houdt om andere mensen te ontmoeten.</li>
      <li>Het is een vereiste dat je een digitale spiegelreflex-camera hebt en lichtsterke lens met vast diafragma van F2.</li>
      <li>8 en natuurlijk een externe flitser (E-TTL).</li>
      <li>Je bent verantwoordelijk voor je eigen vervoer om naar de evenementen te gaan waar je foto's maakt.</li>
    </ul>
  </section>

  <section class="signup">
    <div class="wrap">
      <h2>AANMELDEN</h2>
      <p>Wil jij ook het team van Partyvenz versterken en het nachtleven van een andere kant verkennen? Geef je dan op, stuur een mailtje naar marco@partyvenz.example Vermeld daar goed in je naam, leeftijd, woonplaats en het type camera dat je hebt en je ervaring op het gebied van fotograferen. Bekijk ons online foto album voor de door mij geschoten foto's. Bekijk al mijn ViewTube filmpjes via mijn eigen ViewTube kanaal</p>
    </div>
  </section>

  <section class="events">
    <div class="wrap">
      <h2 class="section-title">EVENTS OF THE PAST</h2>
      <div class="cards">
        <article class="card">
          <div class="card-img" role="img" aria-label="Foto van twee feestgangers in kleurrijke kostuums op straat" style="background:linear-gradient(135deg,#8a7a6a,#c9743a 50%,#5a4a3a)">
            <div class="date"><em>APRIL</em><strong>02</strong><small>2016</small></div>
          </div>
          <h4>FESTIVAL SOL VIBRA 2016</h4>
          <div class="card-meta"><span><svg width="11" height="11" viewBox="0 0 11 11"><rect x=".5" y="1.5" width="10" height="9" fill="none" stroke="#666"/><path d="M.5 4h10" stroke="#666"/></svg>11.00,2.00</span><span><svg width="12" height="11" viewBox="0 0 12 11"><path d="M1.5 1h9a1 1 0 0 1 1 1v5a1 1 0 0 1-1 1H5l-2.5 2.5V8h-1a1 1 0 0 1-1-1V2a1 1 0 0 1 1-1z" fill="none" stroke="#666"/></svg>No comments</span></div>
          <p>Sed ut perspiciatis unde omnis iste natus error sit uptatem accusantium doloremque laudantium, totam rem aperiam, eaque ipsa quae ab illo inventore veritatis</p>
        </article>
        <article class="card">
          <div class="card-img" role="img" aria-label="Foto van een drummer en band op een podium" style="background:linear-gradient(135deg,#2a2a6a,#6a3aa0 50%,#1a1a3a)">
            <div class="date"><em>APRIL</em><strong>02</strong><small>2016</small></div>
          </div>
          <h4>FESTIVAL SOL VIBRA 2016</h4>
          <div class="card-meta"><span><svg width="11" height="11" viewBox="0 0 11 11"><rect x=".5" y="1.5" width="10" height="9" fill="none" stroke="#666"/><path d="M.5 4h10" stroke="#666"/></svg>11.00,2.00</span><span><svg width="12" height="11" viewBox="0 0 12 11"><path d="M1.5 1h9a1 1 0 0 1 1 1v5a1 1 0 0 1-1 1H5l-2.5 2.5V8h-1a1 1 0 0 1-1-1V2a1 1 0 0 1 1-1z" fill="none" stroke="#666"/></svg>No comments</span></div>
          <p>Sed ut perspiciatis unde omnis iste natus error sit uptatem accusantium doloremque laudantium, totam rem aperiam, eaque ipsa quae ab illo inventore veritatis</p>
        </article>
        <article class="card">
          <div class="card-img" role="img" aria-label="Foto van juichend publiek onder confetti" style="background:linear-gradient(135deg,#3a2a6a,#b03a8a 50%,#2a1a3a)">
            <div class="date"><em>APRIL</em><strong>02</strong><small>2016</small></div>
          </div>
          <h4>FESTIVAL SOL VIBRA 2016</h4>
          <div class="card-meta"><span><svg width="11" height="11" viewBox="0 0 11 11"><rect x=".5" y="1.5" width="10" height="9" fill="none" stroke="#666"/><path d="M.5 4h10" stroke="#666"/></svg>11.00,2.00</span><span><svg width="12" height="11" viewBox="0 0 12 11"><path d="M1.5 1h9a1 1 0 0 1 1 1v5a1 1 0 0 1-1 1H5l-2.5 2.5V8h-1a1 1 0 0 1-1-1V2a1 1 0 0 1 1-1z" fill="none" stroke="#666"/></svg>No comments</span></div>
          <p>Sed ut perspiciatis unde omnis iste natus error sit uptatem accusantium doloremque laudantium, totam rem aperiam, eaque ipsa quae ab illo inventore veritatis</p>
        </article>
      </div>
    </div>
  </section>

  <section class="gallery-title"><h2>Our Gallery</h2></section>
  <section class="gallery">
    <div role="img" aria-label="Galerijfoto van een lachende vrouw op een feest" style="background:linear-gradient(135deg,#c0306a,#e8a070 50%,#2a6a8a)"></div>
    <div role="img" aria-label="Galerijfoto van een vrolijk stel" style="background:linear-gradient(135deg,#d8d8c8,#6a4a3a 50%,#2a2a2a)"></div>
    <div role="img" aria-label="Galerijfoto van twee vriendinnen met een drankje" style="background:linear-gradient(135deg,#8a2a2a,#d8a080 50%,#4a2a2a)"></div>
    <div role="img" aria-label="Galerijfoto van een wandelaar bij zonsondergang" style="background:linear-gradient(160deg,#f0d8a0,#c88a4a 55%,#5a3a2a)"></div>
  </section>

  <section class="newsletter">
    <div class="wrap">
      <svg class="nl-icon" width="58" height="48" viewBox="0 0 58 48"><rect x="2" y="8" width="50" height="36" rx="3" fill="#fff" transform="rotate(-12 27 26)"/><path d="M6 14l22 16 22-16" stroke="#ee8625" stroke-width="3" fill="none" transform="rotate(-12 27 26)"/></svg>
      <div class="nl-label"><span>NEWSLETTER</span><strong>SUBSCRIPTION</strong></div>
      <div class="nl-field nl-name">YOUR NAME*</div>
      <div class="nl-field nl-mail">YOUR E-MAIL*</div>
      <div class="nl-btn">SIGN UP</div>
    </div>
  </section>

  <footer class="footer">
    <div class="wrap">
      <div class="socials"><i></i><i></i><i></i><i></i><i></i></div>
      <nav class="footnav">HOME<b>/</b>FREE TICKETS<b>/</b>AGENDA<b>/</b>REVIEWS<b>/</b>CONTACT US</nav>
      <p class="copyright">2016 © Copyrights MarcoV Photography.All Rights Reserved</p>
      <span class="footer-tag">C7</span>
    </div>
  </footer>

</div>
</body>
</html>
```